Beacon Advisory Website

I currently have a website www.beaconadvisoryinc.com. We are a IT Consulting Company. Our website will pretty much tell out our services. I am looking to enhance my website and make it look more professional. Looking for very classy and Contemporary look and design for my website.

It Company

```html
<!DOCTYPE html>
<html lang="en">
<head>
<meta charset="utf-8">
<title>Beacon Advisory</title>
<link href="https://fonts.googleapis.com/css2?family=Source+Sans+3:wght@400;600;700&display=swap" rel="stylesheet">
<style>
:root{
  --navy:#1b5fa5;
  --sky:#1e9ad6;
  --accent:#1a8ccc;
  --ink:#2b2b2b;
  --muted:#6a6a6a;
  --soft:#f4f4f4;
  --white:#ffffff;
  --button:#163e73;
}
*{margin:0;padding:0;box-sizing:border-box}
html,body{width:1200px;height:2647px;overflow:hidden}
body{font-family:"Source Sans 3",sans-serif;color:var(--ink);background:var(--white);position:relative}
section,header,footer{position:absolute;left:0;width:1200px}
.abs{position:absolute}

.site-header{top:0;height:106px;background:var(--white)}
.brand{left:115px;top:34px;display:flex;align-items:center;gap:12px}
.brand-dot{width:36px;height:36px;border-radius:50%;background:var(--accent)}
.brand-name{font-size:26px;font-weight:700;color:var(--navy);letter-spacing:.5px}
.main-nav{left:415px;top:62px;display:flex;gap:44px}
.main-nav a{font-size:13.5px;font-weight:600;color:var(--ink);text-decoration:none;letter-spacing:.3px}

.hero{top:106px;height:499px}
.hero-photo{left:0;top:0;width:1200px;height:499px;background:linear-gradient(100deg,#1c66ae 0%,#2a86c9 45%,#4d9fd8 70%,#2a7cc0 100%)}
.hero-title{left:141px;top:205px;font-size:36px;font-weight:600;color:var(--white);letter-spacing:.5px}
.hero-text{left:146px;top:256px;width:400px;font-size:14px;line-height:25px;color:#e6f1fb}
.btn-solid{left:146px;top:342px;width:138px;height:48px;background:var(--button);color:var(--white);font-size:12.5px;font-weight:700;display:flex;align-items:center;justify-content:center;letter-spacing:.4px}
.hero-dots{left:574px;top:458px;display:flex;gap:8px}
.hero-dots span{width:10px;height:10px;border-radius:50%;background:var(--white)}
.hero-dots span.off{background:rgba(255,255,255,.55)}

.welcome{top:605px;height:339px;background:var(--soft);text-align:center}
.section-title{font-size:22px;font-weight:600;color:var(--accent);letter-spacing:.3px}
.welcome .section-title{position:absolute;left:0;width:1200px;top:58px}
.welcome-text{left:176px;top:130px;width:848px;font-size:13.5px;line-height:24px;color:#555}
.btn-outline{left:545px;top:267px;width:111px;height:37px;border:1px solid #9a9a9a;color:var(--navy);font-size:12px;font-weight:700;display:flex;align-items:center;justify-content:center;background:var(--white)}

.services{top:944px;height:441px;background:var(--white)}
.services .section-title{position:absolute;left:0;width:1200px;top:63px;text-align:center;color:var(--navy)}
.service{top:157px;width:288px}
.service-head{display:flex;align-items:center;gap:12px;height:60px;border-bottom:2px solid var(--accent)}
.service-icon{width:60px;height:60px;border-radius:50%;background:var(--accent);display:flex;align-items:center;justify-content:center}
.service-name{font-size:19px;color:var(--ink);letter-spacing:.3px}
.service-text{margin-top:24px;font-size:11.5px;line-height:19.5px;color:#444}
.service-dots{left:566px;top:399px;display:flex;gap:9px}
.service-dots span{width:9px;height:9px;border-radius:50%;background:#c9c9c9}
.service-dots span.on{background:var(--accent)}

.feature{height:355px}
.feature-photo{width:310px;height:310px;border-radius:50%;border:6px solid var(--white);box-shadow:0 3px 10px rgba(0,0,0,.25)}
.feature-title{font-size:22px;font-weight:600;letter-spacing:.3px}
.feature-text{font-size:13.5px;line-height:24px}
.it-consulting{top:1385px;background:var(--navy);color:var(--white)}
.it-consulting .feature-photo{left:142px;top:22px;background:linear-gradient(160deg,#c8d4de,#6f8396 55%,#3e6a3a)}
.it-consulting .feature-title{left:536px;top:48px}
.it-consulting .feature-text{left:536px;top:119px;width:520px;color:#dfeaf6}
.staff{top:1740px;background:var(--white)}
.staff .feature-title{left:143px;top:62px;color:var(--navy)}
.staff .feature-text{left:143px;top:128px;width:510px;color:#777}
.staff .feature-photo{left:750px;top:26px;width:304px;height:304px;background:linear-gradient(180deg,#cfe1f3,#6b97c4 60%,#2b4f7c)}
.offshore{top:2093px;background:var(--sky);color:var(--white)}
.offshore .feature-photo{left:142px;top:23px;background:linear-gradient(160deg,#f1efe9,#c9c2b6 55%,#8b7f70)}
.offshore .feature-title{left:536px;top:92px}
.offshore .feature-text{left:536px;top:153px;width:520px;color:#eaf6fd}

.site-footer{top:2448px;height:199px;background:#f2f2f2;text-align:center}
.footer-brand{left:0;width:1200px;top:40px;display:flex;justify-content:center;align-items:center;gap:12px}
.footer-nav{left:0;width:1200px;top:104px;display:flex;justify-content:center;gap:20px;font-size:13px;font-weight:600;color:var(--ink)}
.footer-nav .sep{color:#777;font-weight:400}
.copyright{left:0;width:1200px;top:140px;font-size:12.5px;font-weight:700;color:var(--ink)}
</style>
</head>
<body>

<header class="site-header">
  <div class="abs brand"><span class="brand-dot"></span><span class="brand-name">Beacon Advisory</span></div>
  <nav class="abs main-nav">
    <a>COMPANY</a><a>SERVICES</a><a>SOLUTIONS</a><a>RESOURCES</a><a>CAREER</a><a>CONTACT US</a>
  </nav>
</header>

<section class="hero">
  <div class="abs hero-photo" role="img" aria-label="Blue-toned photo of a business professional with overlaid gear shapes"></div>
  <h1 class="abs hero-title">BEACON ADVISORY</h1>
  <p class="abs hero-text">Sed ut perspiciatis unde omnis iste natus error sit voluptatem accusantium doloremque laudantium, totam rem aperiam, eaque ipsa quae ab illo inventore veritatis et quasi architecto</p>
  <div class="abs btn-solid">LEARN MORE</div>
  <div class="abs hero-dots"><span class="off"></span><span></span><span></span><span></span></div>
</section>

<section class="welcome">
  <h2 class="section-title">WELCOME TO BEACON ADVISORY</h2>
  <p class="abs welcome-text">Today's IT market is a dynamic, fast-paced industry, with ever-increasing demands. Meeting these demands for over 25 years, Beacon Advisory maintains a global presence, aggressively recruiting expertly qualified IT and Management Professionals from around the world and cultivating key partnerships with corporations to understand their business models end-to-end, with a goal of delivering exceptional client service and ensuring a consistent delivery of the talent needed to drive results</p>
  <div class="abs btn-outline">LEARN MORE</div>
</section>

<section class="services">
  <h2 class="section-title">OUR SERVICES</h2>
  <div class="abs service" style="left:145px">
    <div class="service-head">
      <span class="service-icon"><svg width="28" height="24" viewBox="0 0 28 24"><rect x="2" y="16" width="4" height="6" fill="#fff"/><rect x="8" y="12" width="4" height="10" fill="#fff"/><rect x="14" y="8" width="4" height="14" fill="#fff"/><rect x="20" y="3" width="4" height="19" fill="#fff"/></svg></span>
      <span class="service-name">BUSINESS</span>
    </div>
    <p class="service-text">Lorem Ipsum is simply dummy text of the printing and typesetting industry. Lorem Ipsum has been the industry's standard dummy text ever since the 1500s, when an unknown printer took a galley of type and scrambled it to make a type specimen book.</p>
  </div>
  <div class="abs service" style="left:453px">
    <div class="service-head">
      <span class="service-icon"><svg width="22" height="30" viewBox="0 0 22 30"><circle cx="11" cy="11" r="8" fill="none" stroke="#fff" stroke-width="2.5"/><rect x="7" y="20" width="8" height="3" fill="#fff"/><rect x="8" y="25" width="6" height="3" fill="#fff"/></svg></span>
      <span class="service-name">TECHNOLOGY</span>
    </div>
    <p class="service-text">Lorem Ipsum is simply dummy text of the printing and typesetting industry. Lorem Ipsum has been the industry's standard dummy text ever since the 1500s, when an unknown printer took a galley of type and scrambled it to make a type specimen book.</p>
  </div>
  <div class="abs service" style="left:768px">
    <div class="service-head">
      <span class="service-icon"><svg width="26" height="26" viewBox="0 0 26 26"><rect x="2" y="5" width="18" height="18" rx="2" fill="none" stroke="#fff" stroke-width="2.5"/><path d="M10 16 L22 4 L24 6 L12 18 L9 19 Z" fill="#fff"/></svg></span>
      <span class="service-name">APPLICATION</span>
    </div>
    <p class="service-text">Lorem Ipsum is simply dummy text of the printing and typesetting industry. Lorem Ipsum has been the industry's standard dummy text ever since the 1500s, when an unknown printer took a galley of type and scrambled it to make a type specimen book.</p>
  </div>
  <div class="abs service-dots"><span class="on"></span><span></span><span></span><span></span></div>
</section>

<section class="feature it-consulting">
  <div class="abs feature-photo" role="img" aria-label="Photo of colleagues working at a laptop in a modern office"></div>
  <h2 class="abs feature-title">IT CONSULTING</h2>
  <div class="abs feature-text">
    <p>Information technology should improve business results. Crestline helps companies make sure it does. We look at IT issues strategically, in the broader context of our clients' business. Our experts provide an objective, independent perspective to help companies realize the full potential of their IT resources, investments and assets.</p>
    <p style="margin-top:24px">We draw on global experience across industries and technologies to help solve companies' most complex IT challenges. More than 40% of our work is done in the context of major transformation in the business or in IT.</p>
  </div>
</section>

<section class="feature staff">
  <h2 class="abs feature-title">STAFF AUGMENTATION</h2>
  <p class="abs feature-text">For years Beacon Advisory has been offering our customers the ability to augment their existing staff with temporary highly skilled IT professionals who can help address immediate short term needs. We know that often our customers have brief spikes in their need for reporting, for example. With internal IT teams focused on more strategic projects, it can be difficult to justify diverting a team member for a few weeks to relieve this short term pressure from business users. This is an ideal situation in which to consider bringing in one of our team.</p>
  <div class="abs feature-photo" role="img" aria-label="Photo of a business team in silhouette before a glass office tower"></div>
</section>

<section class="feature offshore">
  <div class="abs feature-photo" role="img" aria-label="Photo of a businessman reviewing documents at a desk"></div>
  <h2 class="abs feature-title">OFFSHORE</h2>
  <p class="abs feature-text">Our Offshore development model has a unique distinction of providing efficient software solutions with cost and quality advantage, using state-of-the-art technologies, having the capacity to handle large projects and, above all, the ability to execute timely deliveries.</p>
</section>

<footer class="site-footer">
  <div class="abs footer-brand"><span class="brand-dot"></span><span class="brand-name">Beacon Advisory</span></div>
  <nav class="abs footer-nav">
    <span>COMPANY</span><span class="sep">|</span><span>SERVICES</span><span class="sep">|</span><span>SOLUTIONS</span><span class="sep">|</span><span>RESOURCES</span><span class="sep">|</span><span>CAREER</span><span class="sep">|</span><span>CONTACT US</span>
  </nav>
  <p class="abs copyright">© 2016 COMPANY NAME | ALL RIGHTS RESERVED</p>
</footer>

</body>
</html>
```